ORLA - Óptica Médica - web design and concept

Website concept - Create and develop our website design and structure. ORLA is an optical store chain, and we are looking to establish our web and digital concept. In attachment there are several pictures about our stores and our logo.

The website structure should be user friendly. Colors should be light and the design as simple and minimalist as possible. There are different variations of the logothat can be used, check the file.

The website will include optical collections and sun collections as an online store. Also, a medical menu should be considered in order for clients to schedule optometry appointments. There should also be a menu for client assistance where the clients can read about glass maintenance in our workshop.
Updates

Low design quality

Number of Pages Required

5+ page

Font styles to use
Serif
Sans Serif

Requirements
Must have
• Must be user-friendly and minimalist.
• Please USE PICTURES FROM THE BRANDS we sell: MERUN, BOSKA, PNW, KOLE, BAMPE
Nice to have
• Nice to inspire: ZEK glasses (see website https://ch.shopzek.com/en/)
• Nice to inspire: https://merun-eyewear.com/
• Nice to ispire: https://www.pnwglobe.com/en/
Should not have
• Hysteric colors and shapes

```html
<!DOCTYPE html>
<html lang="en">
<head>
<meta charset="utf-8">
<title>ORLA Óptica Médica</title>
<link href="https://fonts.googleapis.com/css2?family=Raleway:wght@400;500;600;700;800&family=Lato:wght@400;700&display=swap" rel="stylesheet">
<style>
:root{
  --gold:#b8894a;
  --gold-soft:#c9a06a;
  --ink:#1d1d1d;
  --text:#555;
  --muted:#888;
  --line:#e6e6e6;
  --cream:#fdf8ef;
  --white:#fff;
  --footer:#1f1f1f;
  --red:#c0392b;
}
*{box-sizing:border-box;margin:0;padding:0}
html,body{width:1200px;height:5248px;overflow:hidden}
body{font-family:"Lato",Arial,sans-serif;color:var(--text);background:var(--white);position:relative}
.abs{position:absolute}
h1,h2,h3,h4{font-family:"Raleway",Arial,sans-serif;color:var(--ink)}
.section-title{position:absolute;left:0;width:1200px;text-align:center;font-size:40px;font-weight:700;letter-spacing:1px}
.btn{display:inline-block;font-family:"Raleway",Arial,sans-serif;font-weight:600;border-radius:40px;text-align:center}
.btn-gold{background:var(--gold);color:var(--white)}
.btn-line{border:2px solid var(--gold-soft);color:var(--gold);background:var(--white)}

/* header */
.site-header{left:0;top:0;width:1200px;height:88px;background:var(--white)}
.brand{left:92px;top:10px;width:60px;text-align:center}
.brand-mark{width:34px;height:34px;border:2px solid var(--ink);margin:0 auto 4px}
.brand-name{font-family:"Raleway",sans-serif;font-size:16px;letter-spacing:4px;color:var(--ink);font-weight:500}
.main-nav{left:374px;top:34px;display:flex;gap:30px;font-family:"Raleway",sans-serif;font-size:14px;font-weight:700;color:var(--ink)}
.nav-icon{top:32px}
.trial{left:940px;top:26px;width:140px;height:36px;line-height:36px;font-size:15px}

/* hero */
.hero{left:0;top:88px;width:1200px;height:465px;background:
  radial-gradient(ellipse 320px 300px at 880px 260px,rgba(190,220,150,.55),transparent 70%),
  radial-gradient(ellipse 260px 320px at 1080px 300px,rgba(40,90,150,.45),transparent 70%),
  linear-gradient(90deg,#23381a 0%,#3d6527 30%,#5f8c3a 55%,#7fa95a 75%,#4f6f3a 100%)}
.hero h1{position:absolute;left:100px;top:135px;font-size:48px;color:var(--white);font-weight:800;letter-spacing:1px}
.hero p{position:absolute;left:100px;top:208px;width:520px;font-size:19px;line-height:30px;color:var(--white);font-weight:700}
.hero .btn{position:absolute;left:100px;top:296px;width:170px;height:44px;line-height:44px;font-size:19px}
.dots{display:flex;gap:6px}
.dot{width:10px;height:10px;border-radius:50%;border:1.5px solid var(--white)}
.dot.on{background:var(--white)}
.hero .dots{position:absolute;left:570px;top:430px}

/* about */
.about-main{left:98px;top:662px;width:428px;height:563px;background:
  radial-gradient(ellipse 200px 120px at 214px 420px,rgba(150,90,45,.9),transparent 75%),
  linear-gradient(180deg,#6b6258 0%,#3a332c 30%,#5a4634 55%,#c9c3b8 78%,#dcd7ce 100%)}
.about h2{position:absolute;left:606px;top:650px;font-size:42px;font-weight:700}
.about p{position:absolute;left:606px;top:722px;width:494px;font-size:14px;line-height:31px;color:var(--text)}
.about .btn{position:absolute;left:606px;top:922px;width:134px;height:38px;line-height:38px;font-size:14px}
.about-small1{left:550px;top:1022px;width:272px;height:203px;background:
  radial-gradient(ellipse 90px 70px at 150px 120px,rgba(70,150,120,.75),transparent 75%),
  linear-gradient(135deg,#f2b24a,#d96a2c 55%,#f1c99a)}
.about-small2{left:843px;top:1022px;width:257px;height:203px;background:
  linear-gradient(180deg,#f6f4f0 0%,#f6f4f0 42%,#3a3530 48%,#e4e0da 56%,#dcd8d1 100%)}

/* products */
.products-title{top:1315px}
.product-card{left:98px;top:1410px;width:1002px;height:325px}
.product-card h3{position:absolute;left:0;top:0;font-size:26px;font-weight:700}
.product-card .desc{position:absolute;left:0;top:50px;width:460px;font-size:14px;line-height:30px}
.stars{position:absolute;left:0;top:200px;color:var(--red);font-size:15px;letter-spacing:1px}
.price{position:absolute;left:0;top:228px;color:var(--red);font-size:17px}
.add-cart{position:absolute;left:0;top:270px;width:114px;height:34px;line-height:34px;font-size:13px}
.buy-now{position:absolute;left:132px;top:270px;width:116px;height:34px;line-height:34px;font-size:13px;background:#ececec;color:var(--ink)}
.product-photo{left:640px;top:1428px;width:452px;height:270px;background:
  radial-gradient(ellipse 140px 70px at 230px 130px,rgba(60,60,150,.7),transparent 75%),
  linear-gradient(180deg,#cbb89a,#b69e7a 60%,#d3c2a6);box-shadow:0 4px 16px rgba(0,0,0,.12)}
.products-dots{left:580px;top:1770px}
.products-dots .dot{border-color:#aaa;width:9px;height:9px}
.products-dots .dot.on{background:#999}

/* arrivals */
.arrivals-title{top:1870px}
.arrival{top:1980px;width:318px;height:210px}
.arrival-photo{position:absolute;left:20px;top:20px;width:278px;height:130px;background:
  radial-gradient(ellipse 120px 40px at 139px 65px,rgba(70,45,30,.55),transparent 75%),linear-gradient(180deg,#fff,#f2f2f2)}
.arrival h4{position:absolute;left:0;width:318px;top:165px;text-align:center;font-size:20px;font-weight:700}
.heart{position:absolute;right:8px;top:0}
.arrow{top:2045px}

/* feature rows */
.feature-photo-1{left:0;top:2282px;width:600px;height:490px;background:
  radial-gradient(ellipse 160px 180px at 300px 230px,rgba(225,215,195,.7),transparent 75%),
  linear-gradient(135deg,#3d3d38,#6e6a5e 50%,#b9b2a2)}
.feature-photo-2{left:600px;top:2772px;width:600px;height:490px;background:
  radial-gradient(ellipse 160px 200px at 300px 260px,rgba(220,170,120,.8),transparent 75%),
  linear-gradient(135deg,#4f7d32,#7c9a4a 50%,#d9c08c)}
.feature-text{width:600px;text-align:center}
.feature-text h3{font-size:28px;font-weight:600;margin-bottom:30px}
.feature-text p{width:420px;margin:0 auto;font-size:13px;line-height:26px}
.feature-text .btn{margin-top:28px;width:118px;height:36px;line-height:32px;font-size:12px;letter-spacing:1px}

/* guarantees */
.guarantees{left:0;top:3262px;width:1200px;height:476px;background:var(--cream)}
.guarantees-title{top:3355px}
.guarantee{top:3478px;width:300px}
.guarantee h4{position:absolute;left:60px;top:0;font-size:20px;font-weight:500;line-height:27px}
.guarantee p{position:absolute;left:60px;font-size:14px;line-height:28px;width:240px;color:var(--ink)}
.guarantee svg{position:absolute;left:0;top:0}

/* brands */
.brands-title{top:3830px}
.brand-logo{top:3938px;width:180px;text-align:center;color:#555;font-family:"Raleway",sans-serif;font-size:22px;font-weight:600;letter-spacing:3px}

/* blog */
.blog-title{top:4185px}
.post{top:4280px;width:280px;height:390px;background:var(--white);box-shadow:0 6px 18px rgba(0,0,0,.15)}
.post-photo{width:280px;height:172px}
.post p{padding:22px 30px 0;font-size:14px;line-height:26px;text-align:center;color:var(--ink)}
.post-meta{position:absolute;left:0;top:318px;width:280px;text-align:center;font-size:12px;color:var(--gold)}

/* footer */
.site-footer{left:0;top:4778px;width:1200px;height:470px;background:var(--footer);color:#ccc}
.site-footer h4{position:absolute;top:52px;font-size:20px;font-weight:500;color:var(--white);font-family:"Raleway",sans-serif}
.site-footer .col{position:absolute;top:112px;font-size:13px;line-height:30px}
.site-footer .row{display:flex;gap:10px;align-items:flex-start}
.site-footer ul{list-style:none}
.site-footer li::before{content:"•";color:var(--gold);margin-right:12px}
.book{left:98px;top:360px;width:208px;height:40px;line-height:40px;font-size:12px;letter-spacing:1px}
.copy{left:0;bottom:20px;width:1200px;text-align:center;font-size:12px;color:#ccc}
</style>
</head>
<body>

<header class="site-header abs">
  <div class="brand abs"><div class="brand-mark"></div><div class="brand-name">ORLA</div></div>
  <nav class="main-nav abs"><span>Home</span><span>About Us</span><span>Products</span><span>Contact</span><span>Blog</span><span>Store</span></nav>
  <svg class="nav-icon abs" style="left:810px" width="20" height="20" viewBox="0 0 20 20"><circle cx="8" cy="8" r="6" fill="none" stroke="#1d1d1d" stroke-width="2.2"/><line x1="12.5" y1="12.5" x2="18" y2="18" stroke="#1d1d1d" stroke-width="2.4"/></svg>
  <svg class="nav-icon abs" style="left:874px" width="22" height="20" viewBox="0 0 22 20"><path d="M1 2h4l3 11h11l2-8H7" fill="none" stroke="#1d1d1d" stroke-width="2"/><circle cx="9" cy="17" r="2" fill="#1d1d1d"/><circle cx="17" cy="17" r="2" fill="#1d1d1d"/></svg>
  <span class="btn btn-gold trial abs">Get Free Trial</span>
</header>

<section class="hero abs" role="img" aria-label="Child blowing a dandelion in a green forest">
  <h1>ORLA OPTICA MEDICA</h1>
  <p>We will be happy to help you and offer you the best solution for your visual health problems.</p>
  <span class="btn btn-gold">Contact Us</span>
  <div class="dots"><span class="dot on"></span><span class="dot"></span><span class="dot"></span><span class="dot"></span></div>
</section>

<section class="about">
  <div class="about-main abs" role="img" aria-label="Interior of the optical store with chandelier and display shelves"></div>
  <h2>ABOUT US</h2>
  <p>Lorem ipsum dolor sit amet, consectetur adipiscing elit, sed do eiusmod tempor incididunt ut labore et dolore magna aliqua. Ut enim ad minim veniam, quis nostrud exercitation ullamco laboris nisi ut aliquip ex ea commodo consequat. Duis aute irure dolor in reprehenderit in voluptate velit esse cillum dolore eu fugiat nulla pariatur.</p>
  <span class="btn btn-gold">READ MORE</span>
  <div class="about-small1 abs" role="img" aria-label="Smiling woman wearing a sun hat and mirrored sunglasses"></div>
  <div class="about-small2 abs" role="img" aria-label="Pair of browline glasses on a light surface"></div>
</section>

<h2 class="section-title products-title">PRODUCTS</h2>
<section class="product-card abs">
  <h3>SUN GLASSES</h3>
  <p class="desc">Protect yourself adequately from ultraviolet (UV) rays thanks to our wide range of glasses, photochromic lenses and polarized lenses. Dress your look with the best quality and with prestigious brands: Hale Ardent, Tomas Riel, Sentry, Clearfield, Corsano...</p>
  <div class="stars">★★★★★</div>
  <div class="price">£349.00</div>
  <span class="btn btn-gold add-cart">Add To Cart</span>
  <span class="btn buy-now">Buy Now</span>
</section>
<div class="product-photo abs" role="img" aria-label="Mirrored sunglasses lying on sand"></div>
<div class="dots products-dots abs"><span class="dot on"></span><span class="dot"></span><span class="dot"></span></div>

<h2 class="section-title arrivals-title">NEW ARRIVALS</h2>
<svg class="arrow abs" style="left:40px" width="16" height="28" viewBox="0 0 16 28"><path d="M13 2L3 14l10 12" fill="none" stroke="#999" stroke-width="2"/></svg>
<svg class="arrow abs" style="left:1144px" width="16" height="28" viewBox="0 0 16 28"><path d="M3 2l10 12L3 26" fill="none" stroke="#999" stroke-width="2"/></svg>
<div class="arrival abs" style="left:72px">
  <div class="arrival-photo" role="img" aria-label="Dark brown sunglasses"></div>
  <svg class="heart" width="20" height="18" viewBox="0 0 20 18"><path d="M10 16S2 11 2 6a4 4 0 0 1 8-1 4 4 0 0 1 8 1c0 5-8 10-8 10z" fill="none" stroke="#333" stroke-width="1.6"/></svg>
  <h4>PERSPICIATIS</h4>
</div>
<div class="arrival abs" style="left:441px">
  <div class="arrival-photo" role="img" aria-label="Black and brown sunglasses"></div>
  <svg class="heart" width="20" height="18" viewBox="0 0 20 18"><path d="M10 16S2 11 2 6a4 4 0 0 1 8-1 4 4 0 0 1 8 1c0 5-8 10-8 10z" fill="none" stroke="#333" stroke-width="1.6"/></svg>
  <h4>PERSPICIATIS</h4>
</div>
<div class="arrival abs" style="left:810px">
  <div class="arrival-photo" role="img" aria-label="Tortoise browline sunglasses"></div>
  <svg class="heart" width="20" height="18" viewBox="0 0 20 18"><path d="M10 16S2 11 2 6a4 4 0 0 1 8-1 4 4 0 0 1 8 1c0 5-8 10-8 10z" fill="none" stroke="#333" stroke-width="1.6"/></svg>
  <h4>PERSPICIATIS</h4>
</div>

<div class="feature-photo-1 abs" role="img" aria-label="Person with windswept hair wearing sunglasses outdoors"></div>
<div class="feature-text abs" style="left:600px;top:2405px">
  <h3>Man and Women Glasses</h3>
  <p>Sed ut perspiciatis unde omnis iste natus error sit voluptatem accusantium doloremque laudantium, totam rem aperiam, eaque ipsa quae ab illo inventore veritatis et quasi architecto.</p>
  <span class="btn btn-line">SHOP NOW</span>
</div>
<div class="feature-text abs" style="left:0;top:2895px">
  <h3>Collection of sunglasses</h3>
  <p>Sed ut perspiciatis unde omnis iste natus error sit voluptatem accusantium doloremque laudantium, totam rem aperiam, eaque ipsa quae ab illo inventore veritatis et quasi architecto.</p>
  <span class="btn btn-line">SHOP NOW</span>
</div>
<div class="feature-photo-2 abs" role="img" aria-label="Woman in sunglasses sitting on grass in the sun"></div>

<section class="guarantees abs"></section>
<h2 class="section-title guarantees-title">OUR GUARANTEES</h2>
<svg class="abs" style="left:40px;top:3488px" width="14" height="22" viewBox="0 0 14 22"><path d="M12 2L3 11l9 9" fill="none" stroke="#111" stroke-width="3"/></svg>
<svg class="abs" style="left:1144px;top:3488px" width="14" height="22" viewBox="0 0 14 22"><path d="M2 2l9 9-9 9" fill="none" stroke="#111" stroke-width="3"/></svg>
<div class="guarantee abs" style="left:108px">
  <svg width="30" height="34" viewBox="0 0 30 34"><circle cx="15" cy="9" r="6" fill="none" stroke="#b8894a" stroke-width="2"/><path d="M6 32V22a9 9 0 0 1 18 0v10" fill="none" stroke="#b8894a" stroke-width="2"/></svg>
  <h4>Orla Childhood<br>Guarantee</h4>
  <p style="top:68px">50% discount on new glasses, if your child's graduation has changed before six months.</p>
</div>
<div class="guarantee abs" style="left:458px">
  <svg width="40" height="30" viewBox="0 0 40 30"><rect x="2" y="8" width="24" height="14" fill="none" stroke="#b8894a" stroke-width="2"/><path d="M26 12h8l4 5v5H26" fill="none" stroke="#b8894a" stroke-width="2"/><circle cx="10" cy="24" r="3" fill="#fdf8ef" stroke="#b8894a" stroke-width="2"/><circle cx="31" cy="24" r="3" fill="#fdf8ef" stroke="#b8894a" stroke-width="2"/></svg>
  <h4>Orla Accident<br>Warranty</h4>
  <p style="top:68px">Did you get off your glasses when you got out of the car? Did your little boy play with his sunglasses?</p>
</div>
<div class="guarantee abs" style="left:826px">
  <svg width="34" height="34" viewBox="0 0 34 34"><circle cx="17" cy="9" r="6" fill="none" stroke="#b8894a" stroke-width="2"/><rect x="4" y="20" width="12" height="12" fill="none" stroke="#b8894a" stroke-width="2"/><rect x="18" y="20" width="12" height="12" fill="none" stroke="#b8894a" stroke-width="2"/></svg>
  <h4>Orla Security</h4>
  <p style="top:40px">If you have suffered a robbery or robbery in your home, you will opt for the replacement of the same product at half price.</p>
</div>

<h2 class="section-title brands-title">OUR BRANDS</h2>
<div class="brand-logo abs" style="left:82px">MERUN</div>
<div class="brand-logo abs" style="left:300px">BOSKA</div>
<div class="brand-logo abs" style="left:510px">PNW</div>
<div class="brand-logo abs" style="left:730px">KOLE</div>
<div class="brand-logo abs" style="left:945px">BAMPE</div>

<h2 class="section-title blog-title">LATEST BLOG</h2>
<article class="post abs" style="left:102px">
  <div class="post-photo" role="img" aria-label="Man in glasses beside an eyelid health headline" style="background:linear-gradient(90deg,#8a6a55 0%,#c9a58a 35%,#4f93c2 55%,#9fc8e2 100%)"></div>
  <p>Lorem ipsum dolor sit amet, consectetur adipiscing elit, sed do eiusmod tempor incididunt</p>
  <div class="post-meta">◯ 15 &nbsp; ▢ March 3,2017</div>
</article>
<article class="post abs" style="left:462px">
  <div class="post-photo" role="img" aria-label="Man in sunglasses beside an opinion headline on sunglasses for children" style="background:linear-gradient(90deg,#7a5a48 0%,#3a72b0 30%,#d84a8a 60%,#e8c84a 100%)"></div>
  <p>Lorem ipsum dolor sit amet, consectetur adipiscing elit, sed do eiusmod tempor incididunt</p>
  <div class="post-meta">◯ 15 &nbsp; ▢ March 3,2017</div>
</article>
<article class="post abs" style="left:822px">
  <div class="post-photo" role="img" aria-label="Man in sunglasses beside a sun protection headline" style="background:linear-gradient(90deg,#7a5a48 0%,#2c5d9e 30%,#e0c040 65%,#e86a3a 100%)"></div>
  <p>Lorem ipsum dolor sit amet, consectetur adipiscing elit, sed do eiusmod tempor incididunt</p>
  <div class="post-meta">◯ 15 &nbsp; ▢ March 3,2017</div>
</article>

<footer class="site-footer abs">
  <h4 style="left:98px">Who We Are</h4>
  <p class="col" style="left:98px;width:230px">ORLA OPTICA opens its doors with a clear purpose: to take care of you. Our priority is your visual health, and for this reason we have the best professionals and the most competitive products to serve your needs.</p>
  <span class="btn btn-gold book abs">BOOK AN APPOINTMENT</span>

  <h4 style="left:388px">Contact Details</h4>
  <div class="col" style="left:388px;width:260px">
    <div class="row"><svg width="12" height="16" viewBox="0 0 12 16" style="margin-top:7px"><path d="M6 15S1 9 1 6a5 5 0 0 1 10 0c0 3-5 9-5 9z" fill="#777"/></svg><span>Address Calle Almendros, 22, Velmora</span></div>
    <div class="row"><svg width="12" height="14" viewBox="0 0 12 14" style="margin-top:8px"><path d="M2 1h3l1 3-2 1a7 7 0 0 0 3 4l1-2 3 1v3c0 1-1 2-2 2C5 13 1 8 1 3c0-1 0-2 1-2z" fill="#777"/></svg><span>Telephone 000 55 01 27</span></div>
    <div class="row"><svg width="14" height="10" viewBox="0 0 14 10" style="margin-top:10px"><rect x="1" y="1" width="12" height="8" fill="none" stroke="#777" stroke-width="1.4"/><path d="M1 1l6 5 6-5" fill="none" stroke="#777" stroke-width="1.4"/></svg><span>orlaoptica@mail.example</span></div>
  </div>

  <h4 style="left:686px">Opening Hours</h4>
  <div class="col" style="left:686px;width:230px">
    <div class="row"><svg width="14" height="14" viewBox="0 0 14 14" style="margin-top:8px"><circle cx="7" cy="7" r="6" fill="none" stroke="#777" stroke-width="1.4"/><path d="M7 3v4h3" fill="none" stroke="#777" stroke-width="1.4"/></svg><span>Monday - Friday: 10:00 - 14:00 &amp;<br>17:00 - 20:30</span></div>
    <div class="row"><svg width="14" height="14" viewBox="0 0 14 14" style="margin-top:8px"><circle cx="7" cy="7" r="6" fill="none" stroke="#777" stroke-width="1.4"/><path d="M7 3v4h3" fill="none" stroke="#777" stroke-width="1.4"/></svg><span>Saturday: 10:00 - 14:00</span></div>
  </div>

  <h4 style="left:956px">Quick Links</h4>
  <ul class="col" style="left:956px;top:108px;line-height:35px">
    <li>Home</li><li>About Us</li><li>Products</li><li>Contact</li><li>Blog</li><li>Store</li>
  </ul>
  <div class="copy abs">© Copyrights 2018 Orlaoptica All Rights Reserved</div>
</footer>

</body>
</html>
```